Mosquito and outdoor pest management

The uploaded logo must be integrated as the main theme of the card. I would like it to be modern and eye catching. Maybe some backround images or light silver metallic background.
Space enough at the base for contact info to be put in- phone numbers,emails,names,website.
Space on the back for short blog and lines for hand writing..calling card.
Commercial- golf courses, schools, outdoor function properties, pre event treatments.
Residential- retirement villages, townhome complexes and general houses
Management

```html
<!DOCTYPE html>
<html lang="en">
<head>
<meta charset="utf-8">
<title>Harbourline Pest Care – Business Card</title>
<link rel="stylesheet" href="https://fonts.googleapis.com/css2?family=Marcellus+SC&display=swap">
<style>
  :root {
    --stage: #3b3b3c;
    --silver-light: #ffffff;
    --silver-mid: #e6e6e6;
    --silver-edge: #c4c4c4;
    --ink: #1f1f21;
    --charcoal: #1f2024;
    --green: #0e8a45;
    --text-light: #f1f1f1;
    --rule: #6f6f6f;
  }
  * { box-sizing: border-box; margin: 0; padding: 0; }
  html, body { width: 1105px; height: 1200px; overflow: hidden; }
  body {
    background: var(--stage);
    font-family: "Marcellus SC", serif;
    color: var(--ink);
    position: relative;
  }
  .card {
    position: absolute;
    left: 193px;
    width: 723px;
    height: 414px;
    overflow: hidden;
    background: radial-gradient(ellipse 70% 75% at 62% 45%, var(--silver-light) 0%, var(--silver-mid) 45%, var(--silver-edge) 100%);
  }
  .card--front { top: 144px; }
  .card--back { top: 601px; }

  .brand {
    position: absolute;
    display: flex;
    align-items: center;
    gap: 12px;
    font-family: "Marcellus SC", serif;
    font-weight: 400;
    color: var(--ink);
    white-space: nowrap;
    line-height: 1;
  }
  .brand__mark {
    display: inline-block;
    background: var(--green);
    flex: none;
  }
  .card--front .brand { left: 28px; top: 48px; font-size: 30px; }
  .card--front .brand__mark { width: 16px; height: 16px; }

  .person { position: absolute; left: 28px; top: 166px; }
  .person__name {
    color: var(--green);
    font-size: 30px;
    line-height: 1;
    letter-spacing: 0.02em;
  }
  .person__role {
    font-size: 22px;
    margin-top: 12px;
  }

  .contact-band {
    position: absolute;
    left: 0; right: 0; bottom: 0;
    height: 130px;
    background: var(--charcoal);
    border-top: 4px solid var(--green);
  }
  .contact-list {
    list-style: none;
    position: absolute;
    left: 30px;
    top: 18px;
  }
  .contact-list li {
    display: flex;
    align-items: center;
    gap: 12px;
    color: var(--text-light);
    font-size: 19px;
    height: 31px;
    letter-spacing: 0.03em;
  }
  .contact-list svg { width: 16px; height: 16px; flex: none; }

  .note-lines { position: absolute; left: 28px; right: 30px; top: 0; }
  .note-lines span {
    position: absolute;
    left: 0; right: 0;
    border-top: 1.5px dotted var(--rule);
  }
  .card--back .brand { left: 145px; top: 306px; font-size: 40px; }
  .card--back .brand__mark { width: 20px; height: 20px; }
</style>
</head>
<body>

<section class="card card--front" aria-label="Card front">
  <div class="brand">Harbourline Pest Care <span class="brand__mark"></span></div>

  <div class="person">
    <div class="person__name">Dana Reed</div>
    <div class="person__role">CEO/Founder</div>
  </div>

  <div class="contact-band">
    <ul class="contact-list">
      <li>
        <svg viewBox="0 0 16 16" aria-hidden="true"><path fill="#0e8a45" d="M3.6 1.2l2.3 2.6-1.3 1.9c.9 2 2.6 3.7 4.6 4.6l1.9-1.3 2.6 2.3-1.4 2.3C7.4 14 2 8.6 1.4 3z"/></svg>
        555 014 2290
      </li>
      <li>
        <svg viewBox="0 0 16 16" aria-hidden="true"><rect x="1" y="3" width="14" height="10" fill="#0e8a45"/><path d="M1.5 3.5L8 9l6.5-5.5" fill="none" stroke="#1f2024" stroke-width="1.3"/></svg>
        HELLO@HARBOURLINECARE.COM
      </li>
      <li>
        <svg viewBox="0 0 16 16" aria-hidden="true"><circle cx="8" cy="8" r="7" fill="#0e8a45"/><path d="M1 8h14M8 1c-3 3.5-3 10.5 0 14M8 1c3 3.5 3 10.5 0 14" fill="none" stroke="#1f2024" stroke-width="1"/></svg>
        WWW.HARBOURLINECARE.COM
      </li>
    </ul>
  </div>
</section>

<section class="card card--back" aria-label="Card back">
  <div class="note-lines" aria-hidden="true">
    <span style="top:55px"></span>
    <span style="top:108px"></span>
    <span style="top:157px"></span>
    <span style="top:208px"></span>
    <span style="top:264px"></span>
  </div>
  <div class="brand">Harbourline Pest Care <span class="brand__mark"></span></div>
</section>

</body>
</html>
```